Need webdesign for service company that provides Car hiring service and transit service

We need a web design for a company that provides airport transit services and transport services including Limo, Corporate cars, Disability transit, Family transit service. We need is a simple and professional design.

Below is site which we like and also offer the same service http://www.ridelarkway.com.au/
Updates

Project Deadline Extended
Reason: Waiting for the Feedback from multiple stakeholders. Need the time to select and approve the design

Target Market(s)

Tourism, Travel

Industry/Entity Type

Airport

Number of Pages Required

3 page

Font styles to use
Decorative
Script

Requirements
Must have
• Simple and Professional, Site we like http://www.ridelarkway.com.au/ and also need to mobile friendly
Should not have
• Shouldn't have too many images

```html
<!DOCTYPE html>
<html lang="en">
<head>
<meta charset="utf-8">
<title>GlideWay – Luxury Airport Car Services</title>
<link rel="stylesheet" href="https://fonts.googleapis.com/css2?family=Roboto:wght@300;400;500;700&family=Satisfy&display=swap">
<style>
:root{
  --orange:#e27a00;
  --ink:#222222;
  --text:#555555;
  --muted:#8a8a8a;
  --dark:#1c1d1f;
  --darker:#111213;
  --light:#f2f2f2;
  --line:#dddddd;
  --white:#ffffff;
}
*{box-sizing:border-box;margin:0;padding:0}
html,body{width:1200px;height:2719px;overflow:hidden;background:var(--white)}
body{position:relative;font-family:"Roboto",Arial,sans-serif;color:var(--text)}
.abs{position:absolute}
.script{font-family:"Satisfy",cursive;font-weight:400}

/* hero */
.hero{left:0;top:0;width:1200px;height:658px}
.hero-photo{position:absolute;inset:0;background:linear-gradient(100deg,#17191b 0%,#2a2d30 45%,#3a3d40 70%,#25272a 100%)}
.brand{left:112px;top:22px;display:flex;align-items:center;gap:14px;color:var(--white);font-size:40px;font-weight:400;letter-spacing:1px}
.brand-mark{width:52px;height:52px;border:3px solid var(--white);border-radius:50%}
.nav-icons{left:893px;top:42px;display:flex;gap:22px;align-items:center}
.login{left:1000px;top:36px;width:88px;height:34px;border:2px solid var(--white);color:var(--white);font-size:13px;font-weight:500;display:flex;align-items:center;justify-content:center;letter-spacing:.5px}
.hero-title{left:112px;top:368px;font-size:44px;color:var(--white)}
.hero-title span{color:var(--orange)}
.hero-text{left:112px;top:450px;width:560px;font-size:16px;line-height:23px;color:#e8e8e8}
.btn-outline{border:2px solid var(--white);color:var(--white);font-size:13px;font-weight:700;display:flex;align-items:center;justify-content:center;letter-spacing:.5px}
.book{left:112px;top:513px;width:118px;height:36px}

.quote{left:780px;top:185px;width:308px;height:386px;background:var(--white);box-shadow:0 4px 14px rgba(0,0,0,.35)}
.quote-head{height:65px;background:#f4f4f4;padding:24px 24px;font-size:19px;font-weight:700;color:var(--ink)}
.field{position:absolute;left:25px;width:257px;height:40px;border:1px solid var(--line);display:flex;align-items:center;background:var(--white)}
.field i{width:38px;height:100%;border-right:1px solid var(--line);display:flex;align-items:center;justify-content:center}
.field span{padding-left:12px;font-size:12px;color:#aaa;white-space:nowrap;overflow:hidden}
.opt{position:absolute;left:25px;font-size:12px;color:#555;display:flex;align-items:center;gap:6px}
.estimate{position:absolute;left:25px;top:274px;width:257px;height:65px;background:var(--orange);color:var(--white);font-size:20px;font-weight:700;display:flex;align-items:center;justify-content:center}
.note{position:absolute;left:0;top:355px;width:100%;text-align:center;font-size:12px;color:#555}

/* private */
.sec-title{width:1200px;left:0;text-align:center}
.private-title{top:696px;font-size:44px;color:var(--ink)}
.rule{left:446px;width:308px;top:750px;height:1px;background:#bbb}
.private-sub{top:766px;font-size:15px;letter-spacing:2.5px;color:#444}
.lead{left:123px;width:954px;text-align:center;font-size:13px;line-height:20px;color:var(--muted)}
.card{top:899px;width:308px;height:308px}
.card .photo{position:absolute;inset:0}
.card .label{position:absolute;left:0;bottom:20px;width:100%;text-align:center;color:var(--white);font-size:15px;font-weight:700}
.arrow{top:1038px}

/* fleet */
.fleet-band{left:0;top:1256px;width:1200px;height:444px;background:linear-gradient(180deg,var(--darker),var(--dark))}
.light-band{left:0;top:1700px;width:1200px;height:352px;background:linear-gradient(180deg,#e6e6e6 0%,#fafafa 30%,#ffffff 100%)}
.fleet-title{top:1298px;font-size:44px;color:var(--white)}
.fleet-lead{top:1384px;color:#6e6e6e}
.view{left:526px;top:1476px;width:148px;height:33px;font-size:12px}
.cars{left:178px;top:1570px;width:852px;height:190px;background:radial-gradient(ellipse at 50% 55%,#2e3033 0%,#121314 60%,rgba(18,19,20,0) 72%)}
.features{left:112px;top:1836px;width:976px;display:flex}
.feature{width:195px;text-align:center;padding:0 14px;font-size:12.5px;line-height:19px;color:#555}
.feature svg{display:block;margin:0 auto 18px}

/* bottom */
.bottom{left:0;top:2052px;width:1200px;height:562px;background:var(--light)}
.testimonial{left:112px;top:2107px;width:456px;height:455px;border:7px solid var(--orange);background:var(--white);text-align:center}
.quote-mark{margin-top:42px;color:var(--orange);font-size:34px;font-weight:700;line-height:20px}
.happy{margin-top:14px;font-size:30px;color:var(--ink)}
.avatar{width:84px;height:84px;border-radius:50%;background:var(--orange);margin:8px auto 0}
.test-text{margin:30px auto 0;width:300px;font-style:italic;font-size:14px;line-height:22px;color:#666}
.test-name{margin-top:20px;font-family:"Satisfy",cursive;font-size:18px;color:var(--orange)}
.test-role{font-size:12px;color:var(--orange)}
.news-title{left:629px;top:2094px;font-size:42px;color:var(--ink)}
.post{left:629px;width:459px}
.post h3{font-size:17px;font-weight:500;color:var(--ink)}
.post .meta{margin-top:6px;font-size:10.5px;color:#777}
.post p{margin-top:13px;font-size:13px;line-height:20px;color:#555}
.post p span{color:var(--orange)}
.sep{left:629px;width:459px;height:1px;background:var(--line)}
.see-all{left:629px;width:459px;top:2527px;text-align:center;font-size:12px;font-weight:700;color:var(--ink);letter-spacing:.5px}

/* footer */
.footer{left:0;top:2614px;width:1200px;height:105px;background:#0b0b0b}
.copy{left:112px;top:2646px;font-size:12px;color:#ccc}
.links{left:112px;top:2668px;font-size:12px;color:#ddd}
.badges{left:867px;top:2648px;display:flex;gap:10px}
.badge{height:34px;background:#8a8a8a;border-radius:3px}
</style>
</head>
<body>

<header class="abs hero">
  <div class="hero-photo" role="img" aria-label="Chauffeur greeting travellers beside a private jet on the tarmac"></div>
  <div class="abs brand"><span class="brand-mark"></span>GlideWay</div>
  <nav class="abs nav-icons" aria-label="Quick menu">
    <svg width="18" height="14" viewBox="0 0 18 14"><path d="M0 1h18M0 7h18M0 13h18" stroke="#fff" stroke-width="2"/></svg>
    <svg width="16" height="16" viewBox="0 0 24 24"><path fill="#fff" d="M6.6 10.8a15 15 0 0 0 6.6 6.6l2.2-2.2a1 1 0 0 1 1-.25 11.4 11.4 0 0 0 3.6.57 1 1 0 0 1 1 1V20a1 1 0 0 1-1 1A17 17 0 0 1 3 4a1 1 0 0 1 1-1h3.5a1 1 0 0 1 1 1c0 1.25.2 2.45.57 3.57a1 1 0 0 1-.25 1z"/></svg>
    <svg width="16" height="16" viewBox="0 0 16 16"><circle cx="6.5" cy="6.5" r="5" stroke="#fff" stroke-width="2" fill="none"/><path d="M10 10l5 5" stroke="#fff" stroke-width="2.4"/></svg>
  </nav>
  <div class="abs login">LOGIN</div>

  <h1 class="abs hero-title script">Luxury Airport <span>Car Services</span></h1>
  <p class="abs hero-text">Nullam ac urna eu felis dapibus condimentum sit amet a augue. Sed non neque elit. Sed ut imperdiet nisi. Proin condimentum fermentum nunc.</p>
  <div class="abs btn-outline book">BOOK NOW!</div>

  <form class="abs quote">
    <div class="quote-head">GET INSTANT QUOTE</div>
    <div class="field" style="top:91px"><i><svg width="14" height="14"><circle cx="7" cy="7" r="5.5" stroke="#333" stroke-width="1.5" fill="none"/></svg></i><span>Origin (Public location or exact...</span></div>
    <div class="field" style="top:159px"><i><svg width="12" height="16" viewBox="0 0 12 16"><path fill="#333" d="M6 0a6 6 0 0 0-6 6c0 4.5 6 10 6 10s6-5.5 6-10a6 6 0 0 0-6-6zm0 8.2A2.2 2.2 0 1 1 6 3.8a2.2 2.2 0 0 1 0 4.4z"/></svg></i><span>Destination (Public location or...</span></div>
    <div class="opt" style="top:206px"><svg width="10" height="10"><path d="M5 0v10M0 5h10" stroke="#333" stroke-width="1.6"/></svg>Add Stops</div>
    <div class="opt" style="top:236px"><svg width="11" height="11"><circle cx="5.5" cy="5.5" r="4.5" stroke="#333" stroke-width="1.4" fill="none"/><path d="M5.5 3v5M3 5.5h5" stroke="#333" stroke-width="1.2"/></svg>Show Other Vehicles</div>
    <div class="estimate">ESATIMATE FARE</div>
    <div class="note">* See price guide for extra</div>
  </form>
</header>

<section>
  <h2 class="abs sec-title script private-title">Private &amp; Business</h2>
  <div class="abs rule"></div>
  <p class="abs sec-title private-sub">PERSONALISED TRANSPORT SERVICE</p>
  <p class="abs lead" style="top:812px">Nam nec tellus a odio tincidunt auctor a ornare odio. Sed non  mauris vitae erat consequat auctor eu in elit. Class aptent taciti sociosqu ad litora torquent per conubia nostra, per inceptos himenaeos. Mauris in erat justo. Nullam ac urna eu felis dapibus condimentum sit amet a augue. Sed non neque elit. Sed ut imperdiet nisi. Proin  velit mauris egestas quam, ut aliquam massa nisl quis neque. Suspendisse in orci enim.</p>

  <svg class="abs arrow" style="left:86px" width="14" height="26" viewBox="0 0 14 26"><path d="M12 2L2 13l10 11" stroke="#444" stroke-width="2" fill="none"/></svg>
  <div class="abs card" style="left:112px"><div class="photo" role="img" aria-label="Passenger in a wheelchair being helped onto a bus" style="background:linear-gradient(160deg,#b8473f,#6e3b36 55%,#3c3a3c)"></div><div class="label">DISABILITY TRANSIT</div></div>
  <div class="abs card" style="left:446px"><div class="photo" role="img" aria-label="Family with suitcases walking through an airport" style="background:linear-gradient(170deg,#c9c7c2,#9a8d86 55%,#4a5a6a)"></div><div class="label">FAMILY TRANSIT</div></div>
  <div class="abs card" style="left:780px"><div class="photo" role="img" aria-label="Couple with luggage walking beside a private jet" style="background:linear-gradient(170deg,#4c86c8,#8fb3d6 45%,#6c6a68 75%,#2f2f30)"></div><div class="label">AIRPORT TRANSFERS</div></div>
  <svg class="abs arrow" style="left:1100px" width="14" height="26" viewBox="0 0 14 26"><path d="M2 2l10 11L2 24" stroke="#444" stroke-width="2" fill="none"/></svg>
</section>

<section>
  <div class="abs fleet-band"></div>
  <div class="abs light-band"></div>
  <h2 class="abs sec-title script fleet-title">Luxurious, Quality vehicles for every client</h2>
  <p class="abs lead fleet-lead">Nam nec tellus a odio tincidunt auctor a ornare odio. Sed non  mauris vitae erat consequat auctor eu in elit. Class aptent taciti sociosqu ad litora torquent per conubia nostra, per inceptos himenaeos. Mauris in erat justo. Nullam ac urna eu felis dapibus condimentum sit amet a augue. Sed non neque elit. Sed ut imperdiet nisi. Proin  velit mauris egestas quam, ut aliquam massa nisl quis neque. Suspendisse in orci enim.</p>
  <div class="abs btn-outline view">VIEW OUR FLEET</div>
  <div class="abs cars" role="img" aria-label="Three black luxury limousines and sedans"></div>

  <div class="abs features">
    <div class="feature">
      <svg width="36" height="32" viewBox="0 0 36 32"><rect x="1" y="8" width="34" height="23" rx="2" fill="#e27a00"/><path d="M12 8V3h12v5" stroke="#e27a00" stroke-width="3" fill="none"/><path d="M1 17h34" stroke="#fff" stroke-width="2"/></svg>
      Executive chauffeur service and airport transfers &amp; corporate limo hire</div>
    <div class="feature">
      <svg width="26" height="34" viewBox="0 0 12 16"><path fill="#e27a00" d="M6 0a6 6 0 0 0-6 6c0 4.5 6 10 6 10s6-5.5 6-10a6 6 0 0 0-6-6zm0 8.2A2.2 2.2 0 1 1 6 3.8a2.2 2.2 0 0 1 0 4.4z"/></svg>
      Limousine hire and executive airport transfers across all of Australia</div>
    <div class="feature">
      <svg width="36" height="36" viewBox="0 0 36 36"><circle cx="18" cy="18" r="16" stroke="#e27a00" stroke-width="3" fill="none"/><path d="M18 8v11l7 4" stroke="#e27a00" stroke-width="3" fill="none"/></svg>
      Real time booking and confirmation system for all of your limousine services</div>
    <div class="feature">
      <svg width="38" height="32" viewBox="0 0 38 32"><path d="M2 8h8l16 16h8M2 24h8l16-16h8" stroke="#e27a00" stroke-width="3" fill="none"/><path d="M30 3l5 5-5 5M30 19l5 5-5 5" stroke="#e27a00" stroke-width="3" fill="none"/></svg>
      The only Australian owned and operated limousine service with a streamlined and secure virtual payment and invoicing system</div>
    <div class="feature">
      <svg width="40" height="32" viewBox="0 0 40 32"><rect x="2" y="3" width="36" height="26" rx="3" stroke="#e27a00" stroke-width="3" fill="none"/><path d="M2 11h36" stroke="#e27a00" stroke-width="4"/><path d="M7 21h10" stroke="#e27a00" stroke-width="3"/></svg>
      No credit card surcharge on any of our limousine hire services</div>
  </div>
</section>

<section>
  <div class="abs bottom"></div>
  <aside class="abs testimonial">
    <div class="quote-mark">&ldquo;</div>
    <h3 class="happy script">Happy Clients</h3>
    <div class="avatar" role="img" aria-label="Client avatar illustration"></div>
    <p class="test-text">This is PixelForge's version of Lorem Ipsum. Proin gravida nibh vel velit auctor fermentum nunc. Etiam pharetra, erat sed fermentum feugiat, velit mauris egestas quam, ut  nisl quis neque. Suspendisse in orci enim.</p>
    <div class="test-name">William Doe</div>
    <div class="test-role">Nulla Etiam pharetra</div>
  </aside>

  <h2 class="abs news-title script">News and Events</h2>
  <article class="abs post" style="top:2166px">
    <h3>Awesome lorem ipsum dolor sit amet dosis nulla neis tises.</h3>
    <div class="meta">Posted By John Smith &nbsp;|&nbsp; 29 July 2017 &nbsp;|&nbsp; 20 Comments</div>
    <p>Nullam ac urna eu felis dapibus condimentum sit amet a augue. Sed non neque elit. Sed ut imperdiet nisi. Proin condimentum fermentum nunc. Etiam pharetra, erat sed fermentum feugiat. <span>[Readmore...]</span></p>
  </article>
  <div class="abs sep" style="top:2314px"></div>
  <article class="abs post" style="top:2352px">
    <h3>Awesome lorem ipsum dolor sit amet dosis nulla neis tises.</h3>
    <div class="meta">Posted By John Smith &nbsp;|&nbsp; 29 July 2017 &nbsp;|&nbsp; 20 Comments</div>
    <p>Nullam ac urna eu felis dapibus condimentum sit amet a augue. Sed non neque elit. Sed ut imperdiet nisi. Proin condimentum fermentum nunc. Etiam pharetra, erat sed fermentum feugiat. <span>[Readmore...]</span></p>
  </article>
  <div class="abs sep" style="top:2501px"></div>
  <div class="abs see-all">SEE ALL NEWS AND EVENTS &#9656;</div>
</section>

<footer>
  <div class="abs footer"></div>
  <p class="abs copy">&copy; Copyright 2017 GlideWay. All Rights Reserved</p>
  <p class="abs links">Home &nbsp;|&nbsp; Sitemap &nbsp;|&nbsp; Privacy Policy &nbsp;|&nbsp; Terms &amp; Conditions</p>
  <div class="abs badges">
    <div class="badge" style="width:34px"></div>
    <div class="badge" style="width:50px"></div>
    <div class="badge" style="width:56px"></div>
    <div class="badge" style="width:54px"></div>
  </div>
</footer>

</body>
</html>
```